Zenqo - revolutionary mobile payment

The app is a P2P money trasfert, without the using of credit card or bank circuits it can transfer electronic money from one person to another consumers simply and immediatelly.
You can use the color you want, but the message we need to transert to consumer is simplicity, safety and coolness.
In attach the logo of the company and the wireframe of thre page of the app.
The goal is to design the page of the app with a clear, simple and intuitive graphic.
Updates

I have upgrade the brief with important information and detail, many thanks

Target Market(s)

all the people

Industry/Entity Type

Credit Card

Requirements
Must have
• You have to design one icon for each button in the first page, (shop is: where to shop)
in the second one a new intuitive image (instead of the hand) that let the user to understand that with a simple swipe he can process the payment
Nice to have
• You can include or esxclude what you want or belive can improve user experience of the app
Should not have
• too much color, too much button or information

```html
<!DOCTYPE html>
<html lang="en">
<head>
<meta charset="utf-8">
<title>Zenqo – Variant Backgrounds</title>
<link rel="stylesheet" href="https://fonts.googleapis.com/css2?family=Questrial&display=swap">
<style>
  :root {
    --page-bg: #efeef2;
    --title: #bdbcc2;
    --status-bg: #0a0a0a;
    --status-text: #ffffff;
    --nav-bg: #ededee;
    --nav-ink: #2a2c33;
    --brand: #1f4f9a;
    --header-bg: rgba(32, 66, 116, 0.92);
    --tile-bg: rgba(28, 52, 104, 0.82);
    --tile-ink: #ffffff;
    --white: #ffffff;
    --muted: #d4ddeb;
    --avatar: #6d7f58;
  }
  * { box-sizing: border-box; margin: 0; padding: 0; }
  html, body {
    width: 1200px; height: 866px; overflow: hidden;
    background: var(--page-bg);
    font-family: "Questrial", "Century Gothic", sans-serif;
  }
  .showcase { position: relative; width: 1200px; height: 866px; }
  .showcase-title {
    position: absolute; top: 14px; left: 0; width: 100%;
    text-align: center; font-weight: 400; font-size: 45px;
    letter-spacing: 1px; color: var(--title);
  }
  .screen {
    position: absolute; top: 194px; width: 271px; height: 480px;
    overflow: hidden; box-shadow: 0 0 0 1px rgba(0,0,0,0.15);
  }
  .screen--forest { left: 99px; }
  .screen--sky { left: 466px; }
  .screen--harbour { left: 827px; }

  .screen-backdrop { position: absolute; inset: 0; }
  .screen--forest .screen-backdrop {
    background:
      radial-gradient(ellipse 80px 140px at 92% 40%, #b7bd3a 0%, rgba(150,160,50,0) 100%),
      linear-gradient(180deg, #2f5b68 0%, #3c5a55 30%, #48523a 60%, #2f2b22 85%, #4a4538 100%);
  }
  .screen--sky .screen-backdrop {
    background:
      radial-gradient(ellipse 120px 50px at 20% 20%, #d6e6f5 0%, rgba(214,230,245,0) 100%),
      radial-gradient(ellipse 140px 60px at 50% 95%, #eef3f8 0%, rgba(238,243,248,0) 100%),
      linear-gradient(180deg, #7fb1e0 0%, #3b7dca 35%, #2f62ac 60%, #93b4d8 85%, #e4ecf4 100%);
  }
  .screen--harbour .screen-backdrop {
    background:
      radial-gradient(ellipse 90px 120px at 85% 70%, #2c6f82 0%, rgba(44,111,130,0) 100%),
      linear-gradient(180deg, #a9c6d4 0%, #7e9aa5 25%, #5d6a6a 50%, #74705f 75%, #8b8372 100%);
  }

  .status-bar {
    position: absolute; top: 0; left: 0; right: 0; height: 21px;
    background: var(--status-bg); color: var(--status-text);
    font-family: "Helvetica Neue", Arial, sans-serif; font-size: 10px;
    display: flex; align-items: center; justify-content: space-between; padding: 0 6px;
  }
  .status-carrier, .status-battery { display: flex; align-items: center; gap: 4px; width: 80px; }
  .status-battery { justify-content: flex-end; }
  .status-time { font-weight: 600; }
  .battery { width: 18px; height: 8px; border: 1px solid #fff; border-radius: 2px; padding: 1px; }
  .battery-level { width: 22%; height: 100%; background: #fff; }

  .nav-bar {
    position: absolute; top: 21px; left: 0; right: 0; height: 31px;
    background: var(--nav-bg); display: flex; align-items: center;
    justify-content: space-between; padding: 0 8px;
  }
  .brand { display: flex; align-items: center; gap: 4px; color: var(--brand); font-size: 13px; font-weight: 400; }
  .brand-dot { width: 12px; height: 12px; border-radius: 50%; background: var(--brand); }

  .profile-header {
    position: absolute; top: 52px; left: 0; right: 0; height: 95px;
    background: var(--header-bg); display: flex; align-items: center; padding: 0 10px; gap: 10px;
  }
  .avatar {
    width: 56px; height: 56px; border-radius: 50%; border: 3px solid var(--white);
    background: radial-gradient(circle at 50% 40%, #c9a48b 0%, #7b8a5e 60%, var(--avatar) 100%);
    flex: none;
  }
  .profile-info { flex: 1; margin-top: -14px; }
  .profile-name { color: var(--white); font-size: 15px; }
  .profile-phone { color: var(--muted); font-size: 9px; margin-top: 3px; letter-spacing: 0.3px; }
  .edit-button {
    width: 22px; height: 22px; border-radius: 50%; background: var(--white);
    display: flex; align-items: center; justify-content: center; flex: none;
  }

  .action-grid {
    position: absolute; top: 173px; left: 21px;
    display: grid; grid-template-columns: 105px 105px; grid-auto-rows: 105px;
    column-gap: 20px; row-gap: 20px;
  }
  .action-tile {
    background: var(--tile-bg); color: var(--tile-ink);
    display: flex; flex-direction: column; align-items: center; justify-content: center;
    font-size: 11px; gap: 6px;
  }
  .action-icon { width: 50px; height: 50px; }
</style>
</head>
<body>
<main class="showcase">
  <h1 class="showcase-title">Variant Backgrounds</h1>

  <!-- Reusable screen markup repeated with three backdrops -->
  <section class="screen screen--forest">
    <div class="screen-backdrop" role="img" aria-label="Blurred photo backdrop in teal, olive and dark brown tones"></div>
    <div class="status-bar">
      <span class="status-carrier">●●●○○ VOLT</span>
      <span class="status-time">4:21 PM</span>
      <span class="status-battery">22% <span class="battery"><span class="battery-level"></span></span></span>
    </div>
    <nav class="nav-bar">
      <svg width="18" height="16" viewBox="0 0 18 16" aria-label="Settings"><circle cx="7" cy="9" r="4.5" fill="none" stroke="#2a2c33" stroke-width="3" stroke-dasharray="2 1.5"/><circle cx="7" cy="9" r="1.6" fill="#2a2c33"/><circle cx="14" cy="4" r="2.6" fill="none" stroke="#2a2c33" stroke-width="1.8" stroke-dasharray="1.3 1"/></svg>
      <span class="brand"><span class="brand-dot"></span>Zenqo</span>
    </nav>
    <header class="profile-header">
      <div class="avatar" role="img" aria-label="User profile photo"></div>
      <div class="profile-info">
        <p class="profile-name">Marco Bellini</p>
        <p class="profile-phone">+39 300 555 0142</p>
      </div>
      <span class="edit-button"><svg width="12" height="12" viewBox="0 0 12 12"><path d="M2 10 L3 7 L8.5 1.5 L10.5 3.5 L5 9 Z" fill="#2a2c33"/></svg></span>
    </header>
    <div class="action-grid">
      <a class="action-tile"><svg class="action-icon" viewBox="0 0 50 50"><rect x="10" y="22" width="34" height="22" rx="2" fill="#fff"/><rect x="13" y="36" width="16" height="2" fill="#2a4478"/><circle cx="36" cy="30" r="5" fill="#2a4478"/><path d="M6 8 Q14 4 22 12 L30 22 L24 26 L18 20 L10 18 Z" fill="#fff" stroke="#2a4478" stroke-width="1.5"/></svg>Pay</a>
      <a class="action-tile"><svg class="action-icon" viewBox="0 0 50 50"><path d="M19 4 h10 v10 h6 L24 25 L13 14 h6 Z" fill="#fff"/><path d="M6 22 h8 l4 6 h14 l4 -6 h8 v22 H6 Z" fill="#fff"/><circle cx="36" cy="35" r="6" fill="#2a4478"/><rect x="10" y="34" width="16" height="2" fill="#2a4478"/><rect x="10" y="38" width="16" height="2" fill="#2a4478"/></svg>Ask</a>
      <a class="action-tile"><svg class="action-icon" viewBox="0 0 50 50"><circle cx="25" cy="13" r="9" fill="#fff"/><path d="M8 46 v-10 q0 -12 17 -12 q17 0 17 12 v10 Z" fill="#fff"/><path d="M22 24 h6 l-1 4 l2 12 l-4 4 l-4 -4 l2 -12 Z" fill="#2a4478"/></svg>Account</a>
      <a class="action-tile"><svg class="action-icon" viewBox="0 0 50 50"><circle cx="25" cy="33" r="13" fill="#fff"/><path d="M25 4 a9 9 0 0 1 9 9 c0 7 -9 17 -9 17 s-9 -10 -9 -17 a9 9 0 0 1 9 -9 Z" fill="#fff" stroke="#2a4478" stroke-width="2"/><circle cx="25" cy="13" r="3.5" fill="#2a4478"/></svg>Shop</a>
    </div>
  </section>

  <section class="screen screen--sky">
    <div class="screen-backdrop" role="img" aria-label="Blurred photo backdrop in bright sky blue and white tones"></div>
    <div class="status-bar">
      <span class="status-carrier">●●●○○ VOLT</span>
      <span class="status-time">4:21 PM</span>
      <span class="status-battery">22% <span class="battery"><span class="battery-level"></span></span></span>
    </div>
    <nav class="nav-bar">
      <svg width="18" height="16" viewBox="0 0 18 16" aria-label="Settings"><circle cx="7" cy="9" r="4.5" fill="none" stroke="#2a2c33" stroke-width="3" stroke-dasharray="2 1.5"/><circle cx="7" cy="9" r="1.6" fill="#2a2c33"/><circle cx="14" cy="4" r="2.6" fill="none" stroke="#2a2c33" stroke-width="1.8" stroke-dasharray="1.3 1"/></svg>
      <span class="brand"><span class="brand-dot"></span>Zenqo</span>
    </nav>
    <header class="profile-header">
      <div class="avatar" role="img" aria-label="User profile photo"></div>
      <div class="profile-info">
        <p class="profile-name">Marco Bellini</p>
        <p class="profile-phone">+39 300 555 0142</p>
      </div>
      <span class="edit-button"><svg width="12" height="12" viewBox="0 0 12 12"><path d="M2 10 L3 7 L8.5 1.5 L10.5 3.5 L5 9 Z" fill="#2a2c33"/></svg></span>
    </header>
    <div class="action-grid">
      <a class="action-tile"><svg class="action-icon" viewBox="0 0 50 50"><rect x="10" y="22" width="34" height="22" rx="2" fill="#fff"/><rect x="13" y="36" width="16" height="2" fill="#2a4478"/><circle cx="36" cy="30" r="5" fill="#2a4478"/><path d="M6 8 Q14 4 22 12 L30 22 L24 26 L18 20 L10 18 Z" fill="#fff" stroke="#2a4478" stroke-width="1.5"/></svg>Pay</a>
      <a class="action-tile"><svg class="action-icon" viewBox="0 0 50 50"><path d="M19 4 h10 v10 h6 L24 25 L13 14 h6 Z" fill="#fff"/><path d="M6 22 h8 l4 6 h14 l4 -6 h8 v22 H6 Z" fill="#fff"/><circle cx="36" cy="35" r="6" fill="#2a4478"/><rect x="10" y="34" width="16" height="2" fill="#2a4478"/><rect x="10" y="38" width="16" height="2" fill="#2a4478"/></svg>Ask</a>
      <a class="action-tile"><svg class="action-icon" viewBox="0 0 50 50"><circle cx="25" cy="13" r="9" fill="#fff"/><path d="M8 46 v-10 q0 -12 17 -12 q17 0 17 12 v10 Z" fill="#fff"/><path d="M22 24 h6 l-1 4 l2 12 l-4 4 l-4 -4 l2 -12 Z" fill="#2a4478"/></svg>Account</a>
      <a class="action-tile"><svg class="action-icon" viewBox="0 0 50 50"><circle cx="25" cy="33" r="13" fill="#fff"/><path d="M25 4 a9 9 0 0 1 9 9 c0 7 -9 17 -9 17 s-9 -10 -9 -17 a9 9 0 0 1 9 -9 Z" fill="#fff" stroke="#2a4478" stroke-width="2"/><circle cx="25" cy="13" r="3.5" fill="#2a4478"/></svg>Shop</a>
    </div>
  </section>

  <section class="screen screen--harbour">
    <div class="screen-backdrop" role="img" aria-label="Blurred photo backdrop in pale blue, grey and sand tones"></div>
    <div class="status-bar">
      <span class="status-carrier">●●●○○ VOLT</span>
      <span class="status-time">4:21 PM</span>
      <span class="status-battery">22% <span class="battery"><span class="battery-level"></span></span></span>
    </div>
    <nav class="nav-bar">
      <svg width="18" height="16" viewBox="0 0 18 16" aria-label="Settings"><circle cx="7" cy="9" r="4.5" fill="none" stroke="#2a2c33" stroke-width="3" stroke-dasharray="2 1.5"/><circle cx="7" cy="9" r="1.6" fill="#2a2c33"/><circle cx="14" cy="4" r="2.6" fill="none" stroke="#2a2c33" stroke-width="1.8" stroke-dasharray="1.3 1"/></svg>
      <span class="brand"><span class="brand-dot"></span>Zenqo</span>
    </nav>
    <header class="profile-header">
      <div class="avatar" role="img" aria-label="User profile photo"></div>
      <div class="profile-info">
        <p class="profile-name">Marco Bellini</p>
        <p class="profile-phone">+39 300 555 0142</p>
      </div>
      <span class="edit-button"><svg width="12" height="12" viewBox="0 0 12 12"><path d="M2 10 L3 7 L8.5 1.5 L10.5 3.5 L5 9 Z" fill="#2a2c33"/></svg></span>
    </header>
    <div class="action-grid">
      <a class="action-tile"><svg class="action-icon" viewBox="0 0 50 50"><rect x="10" y="22" width="34" height="22" rx="2" fill="#fff"/><rect x="13" y="36" width="16" height="2" fill="#2a4478"/><circle cx="36" cy="30" r="5" fill="#2a4478"/><path d="M6 8 Q14 4 22 12 L30 22 L24 26 L18 20 L10 18 Z" fill="#fff" stroke="#2a4478" stroke-width="1.5"/></svg>Pay</a>
      <a class="action-tile"><svg class="action-icon" viewBox="0 0 50 50"><path d="M19 4 h10 v10 h6 L24 25 L13 14 h6 Z" fill="#fff"/><path d="M6 22 h8 l4 6 h14 l4 -6 h8 v22 H6 Z" fill="#fff"/><circle cx="36" cy="35" r="6" fill="#2a4478"/><rect x="10" y="34" width="16" height="2" fill="#2a4478"/><rect x="10" y="38" width="16" height="2" fill="#2a4478"/></svg>Ask</a>
      <a class="action-tile"><svg class="action-icon" viewBox="0 0 50 50"><circle cx="25" cy="13" r="9" fill="#fff"/><path d="M8 46 v-10 q0 -12 17 -12 q17 0 17 12 v10 Z" fill="#fff"/><path d="M22 24 h6 l-1 4 l2 12 l-4 4 l-4 -4 l2 -12 Z" fill="#2a4478"/></svg>Account</a>
      <a class="action-tile"><svg class="action-icon" viewBox="0 0 50 50"><circle cx="25" cy="33" r="13" fill="#fff"/><path d="M25 4 a9 9 0 0 1 9 9 c0 7 -9 17 -9 17 s-9 -10 -9 -17 a9 9 0 0 1 9 -9 Z" fill="#fff" stroke="#2a4478" stroke-width="2"/><circle cx="25" cy="13" r="3.5" fill="#2a4478"/></svg>Shop</a>
    </div>
  </section>
</main>
</body>
</html>
```